New Business Card Design Project

We require a business card design for Vexalund, a newly established Indian company.
Our focus is on the development, manufacturing, and export of a diverse array of pharmaceutical products on a global scale. The card should convey a professional appearance, as our primary markets are in Africa, China, and Southeast Asian nations.
We envision a two-sided business card, with the reverse side dedicated to a logo set against a solid color or an elegantly designed pattern. The corners should be rounded. We would appreciate seeing both horizontal and vertical design options. We trust the designer to utilize their expertise in creating this design.

The content for the business card is included in the attached Word file.

Target Market(s)

Our primary markets are in Africa, China, and Southeast Asian, Latin America, Maldives, Sri Lanka

Industry/Entity Type

Pharmaceutical Manufacturing and Export

Contact Information for Business Card

Colors

Designer to choose colors to be used in the design.

Requirements
Must have
• The reverse side of the business card features solely the logo along with the tagline, "Remedies of Life."
Should not have
• The logo should not exceed two instances, encompassing both the front and back sides of the card.

```html
<!DOCTYPE html>
<html lang="en">
<head>
<meta charset="utf-8">
<title>Vexalund Business Card</title>
<link href="https://fonts.googleapis.com/css2?family=Montserrat:wght@400;500;700;800&display=swap" rel="stylesheet">
<style>
  :root {
    --stage: #d2d1cd;
    --card: #ffffff;
    --brand-blue: #27a9e1;
    --brand-red: #f0604b;
    --ink: #1e1e1e;
  }
  html, body {
    margin: 0;
    padding: 0;
    width: 1200px;
    height: 801px;
    overflow: hidden;
    background: var(--stage);
    font-family: "Montserrat", sans-serif;
  }
  .stage {
    position: relative;
    width: 1200px;
    height: 801px;
  }
  .card {
    position: absolute;
    top: 240px;
    width: 540px;
    height: 310px;
    background: var(--card);
    border-radius: 14px;
    overflow: hidden;
    box-shadow: 0 8px 24px rgba(0,0,0,0.18);
  }
  .card-front { left: 40px; }
  .card-back { left: 620px; }

  .front-wave {
    position: absolute;
    inset: 0;
    width: 540px;
    height: 310px;
  }
  .front-brand {
    position: absolute;
    left: 28px;
    top: 112px;
    width: 220px;
    display: flex;
    align-items: center;
    gap: 10px;
  }
  .brand-dot {
    width: 18px;
    height: 18px;
    border-radius: 50%;
    background: var(--brand-blue);
    flex: none;
  }
  .brand-name {
    font-weight: 800;
    color: var(--brand-blue);
    letter-spacing: 0.5px;
  }
  .front-brand .brand-name { font-size: 34px; }

  .divider {
    position: absolute;
    left: 262px;
    top: 30px;
    width: 1px;
    height: 150px;
    background: var(--brand-blue);
  }
  .contact {
    position: absolute;
    left: 282px;
    top: 26px;
    color: var(--ink);
    font-size: 11.5px;
    line-height: 16px;
  }
  .contact p { margin: 0; }
  .contact .contact-name {
    font-size: 18px;
    line-height: 24px;
    font-weight: 700;
    color: var(--brand-blue);
  }
  .contact-list {
    list-style: none;
    padding: 0;
    margin: 8px 0 0;
  }
  .contact-list li {
    display: flex;
    align-items: center;
    gap: 6px;
  }
  .contact-list svg { width: 11px; height: 11px; flex: none; }
  .contact .contact-address { margin-top: 8px; }

  .back-brand {
    position: absolute;
    inset: 0;
    display: flex;
    flex-direction: column;
    align-items: center;
    justify-content: center;
    gap: 6px;
  }
  .back-brand-row {
    display: flex;
    align-items: center;
    gap: 16px;
  }
  .back-brand .brand-dot { width: 34px; height: 34px; }
  .back-brand .brand-name { font-size: 62px; line-height: 1.1; }
  .tagline {
    margin: 0;
    font-size: 16px;
    font-weight: 500;
    letter-spacing: 3px;
    color: var(--brand-red);
    text-transform: uppercase;
  }
</style>
</head>
<body>
<div class="stage">

  <section class="card card-front">
    <svg class="front-wave" viewBox="0 0 540 310" aria-hidden="true">
      <path d="M0,272 C150,272 250,258 350,238 C430,222 490,218 540,214 L540,310 L0,310 Z" fill="var(--brand-blue)"/>
      <path d="M110,306 C210,276 290,240 360,225 C430,210 480,203 530,198" fill="none" stroke="var(--brand-red)" stroke-width="3"/>
    </svg>

    <div class="front-brand">
      <span class="brand-dot"></span>
      <span class="brand-name">Vexalund</span>
    </div>

    <div class="divider"></div>

    <div class="contact">
      <p class="contact-name">Arjun K. Deshmane</p>
      <p class="contact-role">CEO</p>
      <p class="contact-company">Vexalund</p>
      <ul class="contact-list">
        <li>
          <svg viewBox="0 0 12 12"><path d="M2.5 1 L4.5 1 L5.3 3.4 L4 4.4 C4.6 5.8 6.2 7.4 7.6 8 L8.6 6.7 L11 7.5 L11 9.5 C11 10.3 10.3 11 9.5 11 C5 11 1 7 1 2.5 C1 1.7 1.7 1 2.5 1 Z" fill="var(--brand-blue)"/></svg>
          +919876543210
        </li>
        <li>
          <svg viewBox="0 0 12 12"><rect x="1" y="2.5" width="10" height="7" rx="1" fill="var(--brand-red)"/><path d="M1.5 3 L6 6.5 L10.5 3" fill="none" stroke="#fff" stroke-width="1"/></svg>
          adeshmane@vexalund.com
        </li>
        <li>
          <svg viewBox="0 0 12 12"><circle cx="6" cy="6" r="5" fill="var(--brand-blue)"/><path d="M1 6 H11 M6 1 C3.5 3.5 3.5 8.5 6 11 M6 1 C8.5 3.5 8.5 8.5 6 11" fill="none" stroke="#fff" stroke-width="0.7"/></svg>
          www.vexalund.com
        </li>
      </ul>
      <p class="contact-address">12, Sunrise Colony,<br>Nandgaon, 441203, India</p>
    </div>
  </section>

  <section class="card card-back">
    <div class="back-brand">
      <div class="back-brand-row">
        <span class="brand-dot"></span>
        <span class="brand-name">Vexalund</span>
      </div>
      <p class="tagline">Remedies of Life</p>
    </div>
  </section>

</div>
</body>
</html>
```